Business Card Design needed for start up company Halvora

In need of a new business card designed for a start up company based in Sydney, Halvora is a new start up innovative Company, our mission it to make property accessible for everyday Australian and to become the leading Real Estate platform in Australia. We want it to be fresh and clean.

Industry/Entity Type

Financial

Contact Information for Business Card

Section for Name
Section for Title

HALVORA - The Strength of Pooling
Mobile:
Direct:

Font styles to use
Sans Serif

Colors
33a6d7
0692cd
0255a3
ffffff

Requirements
Must have
• Logo, all business card details

```html
<!DOCTYPE html>
<html lang="en">
<head>
<meta charset="UTF-8">
<title>Halvora Business Card</title>
<link rel="stylesheet" href="https://fonts.googleapis.com/css2?family=Montserrat:wght@800&family=Open+Sans:wght@400;600;700&display=swap">
<style>
  :root {
    --backdrop: #2b2c2e;
    --sky: #33d0e4;
    --ocean: #1f8cc4;
    --brand-blue: #0692cd;
    --navy: #1d3f7a;
    --navy-text: #1e4a8a;
    --accent: #33a6d7;
    --paper: #ffffff;
    --ink: #3a3a3a;
  }
  * { margin: 0; padding: 0; box-sizing: border-box; }
  html, body { width: 1200px; height: 900px; overflow: hidden; }
  body {
    background: var(--backdrop);
    font-family: "Open Sans", Arial, sans-serif;
    position: relative;
  }
  .card {
    position: absolute;
    left: 340px;
    width: 520px;
    height: 297px;
    border-radius: 3px;
    overflow: hidden;
    box-shadow: 0 10px 30px rgba(0,0,0,0.45);
  }
  .card-front {
    top: 110px;
    background: linear-gradient(100deg, var(--sky) 0%, var(--ocean) 100%);
  }
  .card-back {
    top: 493px;
    background: var(--paper);
  }
  .wordmark {
    display: flex;
    align-items: center;
    gap: 8px;
    font-family: "Montserrat", Arial, sans-serif;
    font-weight: 800;
    letter-spacing: 1px;
    line-height: 1;
  }
  .wordmark-dot {
    border-radius: 50%;
    flex: none;
  }
  .card-front .wordmark {
    position: absolute;
    left: 112px;
    top: 104px;
    color: var(--paper);
    font-size: 52px;
  }
  .card-front .wordmark-dot {
    width: 60px;
    height: 60px;
    background: var(--paper);
  }
  .tagline {
    position: absolute;
    left: 218px;
    top: 186px;
    color: var(--paper);
    font-size: 12px;
  }
  .side-band {
    position: absolute;
    left: 0;
    top: 0;
    width: 128px;
    height: 100%;
    background: var(--navy);
  }
  .card-back .wordmark {
    position: absolute;
    left: 78px;
    top: 96px;
    color: var(--navy-text);
    font-size: 40px;
  }
  .card-back .wordmark-dot {
    width: 72px;
    height: 72px;
    background: var(--accent);
    border: 4px solid var(--paper);
  }
  .contact {
    position: absolute;
    right: 26px;
    top: 42px;
    text-align: right;
    color: var(--ink);
    font-size: 11.5px;
    line-height: 1.45;
  }
  .contact-name {
    color: var(--navy-text);
    font-weight: 700;
    font-size: 14px;
    letter-spacing: 0.3px;
  }
  .contact-title {
    color: var(--accent);
    font-size: 12.5px;
    margin-bottom: 6px;
  }
  .contact-line {
    display: flex;
    justify-content: flex-end;
    align-items: center;
    gap: 6px;
  }
  .contact-line svg { width: 10px; height: 10px; fill: var(--navy); flex: none; }
  .contact-line.no-icon { padding-right: 16px; }
</style>
</head>
<body>

<section class="card card-front" aria-label="Business card front">
  <div class="wordmark"><span class="wordmark-dot"></span>HALVORA</div>
  <p class="tagline">The Strength of Pooling</p>
</section>

<section class="card card-back" aria-label="Business card back">
  <div class="side-band"></div>
  <div class="wordmark"><span class="wordmark-dot"></span>HALVORA</div>

  <div class="contact">
    <p class="contact-name">MARCUS ELLERY</p>
    <p class="contact-title">CEO/FOUNDER</p>
    <p class="contact-line no-icon">41 Harbour View Street</p>
    <p class="contact-line no-icon">Sydney, NSW 2000</p>
    <p class="contact-line">02 8123 4567
      <svg viewBox="0 0 10 10" aria-hidden="true"><path d="M1 3 Q5 0 9 3 L8 4.5 L6.5 3.8 L6.5 3 Q5 2.5 3.5 3 L3.5 3.8 L2 4.5 Z M2.5 5 H7.5 L8.5 9 H1.5 Z"/></svg>
    </p>
    <p class="contact-line">0412 555 019
      <svg viewBox="0 0 10 10" aria-hidden="true"><path d="M3 0.5 H7 Q8 0.5 8 1.5 V8.5 Q8 9.5 7 9.5 H3 Q2 9.5 2 8.5 V1.5 Q2 0.5 3 0.5 Z M3 2 V7.5 H7 V2 Z"/></svg>
    </p>
    <p class="contact-line">hello@halvora.com.au
      <svg viewBox="0 0 10 10" aria-hidden="true"><path d="M0.5 2 H9.5 V8 H0.5 Z M1 2.4 L5 5.5 L9 2.4 V3.2 L5 6.3 L1 3.2 Z" fill-rule="evenodd"/></svg>
    </p>
    <p class="contact-line">www.halvora.com.au
      <svg viewBox="0 0 10 10" aria-hidden="true"><circle cx="5" cy="5" r="4.5"/></svg>
    </p>
  </div>
</section>

</body>
</html>
```